New Website for novelty yarn producer

We need a new website for our company, Vedrana. We make highly tailored yarns for weavers worldwide. This year marks our 40th anniversary and we want to evolve our image and identity.

Our temporary website can be found at:
www.vedranathreads.example

Our only concern in that throughout the website the protagonist must be our client, we make their creations possible and are highly adaptable both during the ideation process of the yarn as well as in the production. This is at the core of the way we do business and is summarised within the concept of FMC (Full Motion Craft).

Industry/Entity Type

Textile

Number of Pages Required

1 page

Colors
9bcb3c

Requirements
Must have
• Full Motion Craft (FMC) - can be found on or current website www.vedranathreads.example

```html
<!DOCTYPE html>
<html lang="en">
<head>
<meta charset="utf-8">
<title>Vedrana – Novelty Yarn Solutions</title>
<link href="https://fonts.googleapis.com/css2?family=Lato:wght@300;400;700;900&display=swap" rel="stylesheet">
<style>
:root{
  --green:#8cc63f;
  --ink:#2b2b2b;
  --text:#3a3a3a;
  --grey-bg:#ececec;
  --icon:#5b5b5b;
  --white:#ffffff;
  --header:rgba(40,40,40,.78);
}
*{margin:0;padding:0;box-sizing:border-box}
html,body{width:1200px;height:2586px;overflow:hidden}
body{font-family:"Lato",sans-serif;color:var(--text);background:var(--white);position:relative}
.abs{position:absolute}
.btn{position:absolute;background:var(--green);color:var(--white);font-weight:700;font-size:15px;text-transform:uppercase;display:flex;align-items:center;justify-content:center;letter-spacing:.3px}
.center{text-align:center}

/* hero */
.hero-photo{left:0;top:0;width:1200px;height:660px;background:linear-gradient(120deg,#e9e6e2 0%,#d8d3cf 30%,#b84aa0 45%,#3b8fd0 58%,#e6463c 68%,#f39a24 78%,#2fa978 88%,#d7d0ca 100%)}
.site-header{left:0;top:0;width:1200px;height:131px;background:var(--header)}
.brand{left:74px;top:38px;color:var(--white);font-weight:400;font-size:46px;letter-spacing:0;line-height:1}
.brand-sub{left:74px;top:92px;color:var(--white);font-size:9px;letter-spacing:3.4px;font-weight:400}
.nav{left:643px;top:48px;display:flex}
.nav a{color:var(--white);text-decoration:none;font-size:13.5px;font-weight:700;height:35px;display:flex;align-items:center;padding:0 16px;margin-right:8px}
.nav a.active{background:var(--green)}
.hero-line{left:74px;background:var(--green);color:var(--white);font-weight:700;font-size:55px;line-height:1;padding:0 12px;display:flex;align-items:center}
.dot{top:607px;width:14px;height:14px;border-radius:50%;background:#8a8a8a}
.dot.on{background:var(--green)}

/* sections */
h2{font-weight:700;color:var(--ink);font-size:27px;letter-spacing:.5px}
.para{font-size:15px;line-height:25px;color:var(--text)}
.band-green{left:0;top:941px;width:510px;height:336px;background:var(--green)}
.band-grey{left:510px;top:941px;width:690px;height:336px;background:var(--grey-bg)}
.fmc-name{left:0;top:1070px;width:510px;color:var(--white);font-weight:300;font-size:33px;line-height:38px;letter-spacing:.5px;text-align:center}
.feature-title{color:var(--green);font-weight:700;font-size:19px;letter-spacing:.5px}
.heritage-text{left:0;top:1595px;width:600px;height:334px;background:var(--grey-bg)}
.heritage-photo{left:600px;top:1595px;width:600px;height:334px;background:linear-gradient(180deg,#9aa3ad 0%,#e7e6e2 35%,#bfc3c6 60%,#3c4a4c 100%)}
.stat-num{color:var(--green);font-weight:900;font-size:48px;line-height:1}
.stat-label{font-size:14.5px;color:var(--ink)}

/* footer */
.site-footer{left:0;top:2345px;width:1200px;height:241px;background:var(--green)}
.foot-brand{left:74px;top:2390px;font-size:34px;line-height:1;color:var(--white);font-weight:400}
.foot-small{left:74px;font-size:11.5px;color:var(--white);line-height:19px}
.foot-title{font-weight:700;font-size:14px;letter-spacing:.5px;color:var(--white)}
.foot-link{font-size:13.5px;color:var(--white);line-height:24px}
.social{top:2424px;width:20px;height:20px;border-radius:50%;background:var(--white)}
</style>
</head>
<body>

<div class="abs hero-photo" role="img" aria-label="Photo of hands holding colourful balls of yarn"></div>
<header class="abs site-header"></header>
<div class="abs brand">VEDRANA</div>
<div class="abs brand-sub">NOVELTY YARN SOLUTIONS</div>
<nav class="abs nav">
  <a class="active">HOME</a><a>ABOUT US</a><a>FULL MOTION CRAFT</a><a>MORE &nbsp;⌄</a>
</nav>
<div class="abs hero-line" style="top:312px;height:66px">Tailored Weaving</div>
<div class="abs hero-line" style="top:385px;height:66px">Solutions</div>
<div class="abs dot on" style="left:76px"></div>
<div class="abs dot" style="left:99px"></div>
<div class="abs dot" style="left:122px"></div>
<div class="abs dot" style="left:145px"></div>

<!-- welcome -->
<h2 class="abs center" style="left:0;width:1200px;top:703px">WELCOME TO OUR WEBSITE</h2>
<p class="abs para center" style="left:78px;width:1044px;top:746px">Aliquam molestie, mi et imperdiet euismod, dui purus auctor tellus, et interdum lacus lectus et ante. Sed accumsan sollicitudin sapien, sit amet adipiscing turpis gravida ac. In congue, neque ac lobortis volutpat, libero mauris varius mi, vitae suscipit ipsum ligula vitae risus. Duis aliquam nibh a dui iaculis viverra id a velit. Vivamus egestas risus in magna varius commodo. Sed semper viverra egestas.</p>
<div class="btn" style="left:524px;top:846px;width:152px;height:42px">Read More</div>

<!-- FMC band -->
<div class="abs band-green"></div>
<div class="abs band-grey"></div>
<div class="abs fmc-name">FULL<br>MOTION<br>CRAFT</div>
<h2 class="abs center" style="left:510px;width:690px;top:1028px">PRODUCTION BUILT AROUND YOU</h2>
<p class="abs para center" style="left:545px;width:620px;top:1074px">Versatility and flexibility both in development and production are key in delivering a custom solution capable of giving life to your products.</p>
<div class="btn" style="left:753px;top:1145px;width:152px;height:41px">Find Out More</div>

<!-- features -->
<svg class="abs" style="left:212px;top:1334px" width="56" height="58" viewBox="0 0 56 58" aria-hidden="true" fill="var(--icon)">
  <circle cx="13" cy="7" r="6"/><circle cx="43" cy="7" r="6"/>
  <path d="M4 16h18l8 12-4 3-6-8v35h-5V40h-2v18H8V28l-4 10H0z"/>
  <path d="M52 16H34l-8 12 4 3 6-8v35h5V40h2v18h5V28l3 8V16z"/>
  <rect x="33" y="34" width="13" height="10" rx="1"/>
</svg>
<svg class="abs" style="left:580px;top:1334px" width="36" height="58" viewBox="0 0 36 58" aria-hidden="true" fill="none" stroke="var(--icon)" stroke-width="4">
  <path d="M18 3a15 15 0 0 0-9 27c2 2 3 5 3 8h12c0-3 1-6 3-8A15 15 0 0 0 18 3z"/>
  <path d="M12 44h12M13 50h10M15 55h6" stroke-linecap="round"/>
</svg>
<svg class="abs" style="left:928px;top:1338px" width="62" height="52" viewBox="0 0 62 52" aria-hidden="true" fill="var(--icon)">
  <path d="M22 2h18a3 3 0 0 1 3 3v6h-5V7H24v4h-5V5a3 3 0 0 1 3-3z"/>
  <rect x="0" y="12" width="62" height="40" rx="5"/>
  <rect x="14" y="12" width="4" height="40" fill="#fff"/><rect x="44" y="12" width="4" height="40" fill="#fff"/>
</svg>
<div class="abs feature-title center" style="left:90px;width:300px;top:1416px">EXPERIENCE</div>
<div class="abs feature-title center" style="left:448px;width:300px;top:1416px">CREATIVITY</div>
<div class="abs feature-title center" style="left:808px;width:300px;top:1416px">PROFESSIONALITY</div>
<p class="abs para center" style="left:92px;width:296px;top:1448px">Over the years the company has gained the knowledge and skills that define the superiority of our product and the rigor of our work ethic..</p>
<p class="abs para center" style="left:452px;width:292px;top:1448px">Our belief is that the key to our clients' success is a combination of innovation, creativity and quality. We strive to adapt and re-imagine our product...</p>
<p class="abs para center" style="left:808px;width:300px;top:1448px">We are a family business at the core.<br>Our company is run with the same values as the Ferrando family: respect, determination and commitment.</p>

<!-- heritage -->
<div class="abs heritage-text"></div>
<div class="abs heritage-photo" role="img" aria-label="Photo of a spinning mill with rows of white yarn bobbins"></div>
<h2 class="abs center" style="left:0;width:644px;top:1651px">HERITAGE</h2>
<p class="abs para center" style="left:78px;width:488px;top:1696px">Our team has decades of experience in providing yarn solutions to weavers around the world, assisting them in the creation of outstanding textiles. Our clients can expect open lines of communication, clarity and professionality</p>
<div class="btn" style="left:246px;top:1823px;width:152px;height:41px">Our Heritage</div>

<!-- numbers -->
<h2 class="abs center" style="left:0;width:1200px;top:1975px">VTS IN NUMBERS</h2>
<svg class="abs" style="left:214px;top:2048px" width="46" height="60" viewBox="0 0 46 60" aria-hidden="true">
  <rect x="0" y="0" width="46" height="60" rx="2" fill="var(--icon)"/>
  <g fill="#fff">
    <rect x="7" y="7" width="7" height="6"/><rect x="19" y="7" width="7" height="6"/><rect x="31" y="7" width="7" height="6"/>
    <rect x="7" y="18" width="7" height="6"/><rect x="19" y="18" width="7" height="6"/><rect x="31" y="18" width="7" height="6"/>
    <rect x="7" y="29" width="7" height="6"/><rect x="19" y="29" width="7" height="6"/><rect x="31" y="29" width="7" height="6"/>
    <rect x="7" y="40" width="7" height="6"/><rect x="31" y="40" width="7" height="6"/>
    <rect x="18" y="46" width="10" height="14"/>
  </g>
</svg>
<svg class="abs" style="left:566px;top:2048px" width="66" height="62" viewBox="0 0 66 62" aria-hidden="true">
  <circle cx="28" cy="28" r="26" fill="var(--icon)"/>
  <path d="M6 20c14-4 30 2 42 14M4 32c14-2 26 4 36 16M14 8c12 4 24 14 30 28M30 3c6 8 14 20 16 34" fill="none" stroke="#fff" stroke-width="2"/>
  <path d="M46 50c6 6 12 8 18 6" fill="none" stroke="var(--icon)" stroke-width="3" stroke-linecap="round"/>
</svg>
<svg class="abs" style="left:930px;top:2048px" width="58" height="58" viewBox="0 0 58 58" aria-hidden="true">
  <path d="M2 4a2 2 0 0 1 2-2h22l30 30-24 24L2 26z" fill="var(--icon)"/>
  <circle cx="14" cy="14" r="5" fill="#fff"/>
</svg>
<div class="abs stat-num center" style="left:90px;width:300px;top:2122px">40</div>
<div class="abs stat-num center" style="left:448px;width:300px;top:2122px">2</div>
<div class="abs stat-num center" style="left:808px;width:300px;top:2122px">8</div>
<div class="abs stat-label center" style="left:90px;width:300px;top:2182px">YEARS IN BUSINESS</div>
<div class="abs stat-label center" style="left:448px;width:300px;top:2182px">MILLION KILOGRAMS/ YR</div>
<div class="abs stat-label center" style="left:808px;width:300px;top:2182px">BRANDS</div>
<div class="btn" style="left:524px;top:2247px;width:152px;height:41px">Find Out More</div>

<!-- footer -->
<footer class="abs site-footer"></footer>
<div class="abs foot-brand">VEDRANA</div>
<div class="abs foot-small" style="top:2456px">Copyright © 2018. Company Name.<br>All Right Reserved</div>
<div class="abs foot-small" style="top:2503px">R.E.A VD 410932 - Reg. Imp. VD 04712390215<br>P.IVA 00482170633 - Cod. Fisc. 04712390215<br>Capitale sociale € 84.200,00 int. ver.</div>

<div class="abs foot-title" style="left:402px;top:2385px">SITE MAP</div>
<div class="abs foot-link" style="left:402px;top:2409px">Home</div>
<div class="abs foot-link" style="left:402px;top:2436px">About Us</div>
<div class="abs foot-link" style="left:402px;top:2464px">Full Motion Craft</div>
<div class="abs foot-link" style="left:402px;top:2491px">More</div>

<div class="abs foot-title" style="left:645px;top:2385px">CONTACT INFO</div>
<div class="abs foot-link" style="left:645px;top:2409px;font-weight:700">Vedrana Novelty Yarn Solutions</div>
<div class="abs foot-link" style="left:645px;top:2433px">Via dei Telai 14 - 50100<br>Valdoro - Italy</div>
<svg class="abs" style="left:645px;top:2489px" width="13" height="13" viewBox="0 0 24 24" aria-hidden="true"><path fill="#fff" d="M6.6 10.8a15 15 0 0 0 6.6 6.6l2.2-2.2c.3-.3.7-.4 1-.2 1.1.4 2.3.6 3.6.6.6 0 1 .4 1 1V20c0 .6-.4 1-1 1A17 17 0 0 1 3 4c0-.6.4-1 1-1h3.5c.6 0 1 .4 1 1 0 1.3.2 2.5.6 3.6.1.3 0 .7-.2 1z"/></svg>
<div class="abs foot-link" style="left:678px;top:2483px">Tel. 0555 21840 r.a</div>
<svg class="abs" style="left:645px;top:2518px" width="14" height="13" viewBox="0 0 24 22" aria-hidden="true"><path fill="#fff" d="M6 0h10l3 3v5H6zM2 9h20a2 2 0 0 1 2 2v9a2 2 0 0 1-2 2H2a2 2 0 0 1-2-2v-9a2 2 0 0 1 2-2zm4 4v6h12v-6z"/></svg>
<div class="abs foot-link" style="left:678px;top:2512px">Fax 0555 218499</div>

<div class="abs foot-title" style="left:933px;top:2385px">FOLLOW US</div>
<div class="abs social" role="img" aria-label="Social link" style="left:930px"></div>
<div class="abs social" role="img" aria-label="Social link" style="left:964px"></div>
<div class="abs social" role="img" aria-label="Social link" style="left:1002px"></div>
<div class="abs social" role="img" aria-label="Social link" style="left:1041px"></div>
<div class="abs social" role="img" aria-label="Social link" style="left:1092px"></div>

</body>
</html>
```